QuillVane needs a dashboard page designed

Redesign the dashboard shown in the provided images.

There are two images:
- dashboard.png
- dashboard-expanded.png

NOTE: The vocabulary navigation on the left will be a very long list of words 100s, so keep that in mind when you're designing both the vocab navigation and the expanded vocab popup.

In the dashboard.png picture, there needs to be a progress chart showing the word progress like the following: review 1(show it as completed) -> review 2(show the user they are here) -> review 3(unvisited) -> review 4(unvisited)

The do-not-design-this-page.png image is for your reference only. It is not to be designed. Use it to understand the overall look and feel of the website to help you create the best dashboard page possible.
Updates

Need extra days to review

Industry/Entity Type

Education English learning

Number of Pages Required

1 page

Requirements
Must have
• The main navigation and main header cannot change between pages. See the do-not-design page for the main navigateion and header.
Should not have
• Do not add a person profile. We will not have images of our users. Keep the icons in the main navigation as they are.

```html
<!DOCTYPE html>
<html lang="en">
<head>
<meta charset="utf-8">
<title>QuillVane – Vocabulary Dashboard</title>
<link rel="stylesheet" href="https://fonts.googleapis.com/css2?family=Montserrat:wght@400;500;600;700&display=swap">
<style>
  :root{
    --ink:#1f1f1f;
    --bar-dark:#1c1a1a;
    --white:#ffffff;
    --panel:#e1f3fc;
    --muted:#8a8a8a;
    --rule:#cfe2ee;
    --blue:#0a7ac4;
    --orange:#ff9800;
    --grey-step:#d7d7d7;
    --band-long:#e6ecfb;
    --band-work:#d6fff8;
    --band-short:#fbfde6;
    --band-forgot:#ddfaf7;
  }
  *{box-sizing:border-box;margin:0;padding:0}
  html,body{width:1200px;height:836px;overflow:hidden;background:var(--white)}
  body{position:relative;font-family:"Montserrat",sans-serif;color:var(--ink)}

  .top-bar{position:absolute;left:0;top:0;width:1200px;height:47px;background:var(--bar-dark)}
  .brand{position:absolute;left:80px;top:11px;font-size:20px;font-weight:700;color:var(--white);letter-spacing:-.2px}
  .top-actions{position:absolute;right:36px;top:14px;display:flex;gap:17px}
  .top-actions svg{width:18px;height:18px;fill:var(--white)}

  .side-nav{position:absolute;left:0;top:47px;width:80px;height:789px;background:var(--bar-dark)}
  .nav-item{position:absolute;left:0;width:80px;text-align:center;color:var(--white);font-size:9px;font-weight:600}
  .nav-item svg{display:block;margin:0 auto 3px;width:16px;height:16px;fill:var(--white)}

  .vocab-panel{position:absolute;left:109px;top:63px;width:206px;height:691px;background:var(--panel);border-radius:6px}
  .filter{position:absolute;left:13px;top:12px;width:64px;height:28px;border:1.5px solid var(--blue);border-radius:14px;font-size:13px;display:flex;align-items:center;padding-left:10px;gap:14px}
  .expand{position:absolute;left:127px;top:19px;font-size:10px;font-weight:500;display:flex;gap:6px;align-items:center}
  .vocab-list{position:absolute;left:4px;right:0;top:64px}
  .group-head{height:28px;display:flex;align-items:center;font-size:10px;font-weight:500;padding-left:5px;border-bottom:1px solid var(--rule);position:relative;white-space:nowrap}
  .group-head svg{width:10px;height:10px;margin-right:8px;flex:none}
  .group-head .help{position:absolute;left:164px;top:8.5px;width:11px;height:11px;border-radius:50%;background:var(--ink);color:var(--white);font-size:8px;font-weight:700;text-align:center;line-height:11px}
  .group{margin-bottom:21px}
  .word{height:21px;line-height:21px;font-size:11px;color:var(--muted);padding-left:23px;border-bottom:1px solid var(--rule)}

  .steps{position:absolute;left:435px;top:77px;width:616px;height:70px}
  .step-line{position:absolute;top:18px;height:4px;background:var(--grey-step)}
  .step-line.done{background:var(--blue)}
  .step{position:absolute;top:0;width:80px;margin-left:-40px;text-align:center;font-size:12.5px}
  .step .dot{width:40px;height:40px;margin:0 auto 6px;border-radius:50%;background:var(--grey-step);color:var(--white);font-weight:700;font-size:15px;line-height:40px}
  .step.done .dot{background:var(--blue)}
  .step.current .dot{background:var(--orange)}

  .word-card{position:absolute;left:320px;top:158px;width:848px;height:140px;background:var(--panel);border-radius:8px}
  .word-title{position:absolute;left:20px;top:18px;display:flex;align-items:center;gap:10px;font-size:20px;font-weight:600}
  .word-title svg{width:20px;height:20px;fill:var(--orange)}
  .cta{position:absolute;left:549px;top:18px;width:272px;height:33px;border-radius:17px;background:var(--orange);font-size:13px;font-weight:500;display:flex;align-items:center;justify-content:center;color:var(--ink)}
  .word-card p{position:absolute;left:24px;top:72px;width:800px;font-size:11.6px;line-height:14.6px}

  .curve-card{position:absolute;left:320px;top:304px;width:848px;height:346px;background:var(--panel);border-radius:8px}
  .curve-card svg{display:block;width:848px;height:346px;font-family:"Montserrat",sans-serif}

  .analysis{position:absolute;left:337px;top:658px;width:800px}
  .analysis h2{font-size:20px;font-weight:600;margin-bottom:8px}
  .analysis p{font-size:11.6px;line-height:14.6px}

  .footer{position:absolute;left:0;right:0;top:796px;padding-left:80px;text-align:center;font-size:13px}
</style>
</head>
<body>
  <header class="top-bar">
    <div class="brand">QuillVane</div>
    <div class="top-actions">
      <svg viewBox="0 0 24 24" aria-label="Settings"><path d="M19.4 13a7.5 7.5 0 0 0 0-2l2.1-1.6-2-3.5-2.5 1a7 7 0 0 0-1.7-1L15 3h-4l-.4 2.9a7 7 0 0 0-1.7 1l-2.5-1-2 3.5L6.6 11a7.5 7.5 0 0 0 0 2l-2.1 1.6 2 3.5 2.5-1a7 7 0 0 0 1.7 1L11 21h4l.4-2.9a7 7 0 0 0 1.7-1l2.5 1 2-3.5zM13 15.5a3.5 3.5 0 1 1 0-7 3.5 3.5 0 0 1 0 7z"/></svg>
      <svg viewBox="0 0 24 24" aria-label="Messages"><path d="M12 3C6.5 3 2 6.6 2 11c0 2.2 1.1 4.2 3 5.6L4 21l4.6-2.5c1.1.3 2.2.5 3.4.5 5.5 0 10-3.6 10-8s-4.5-8-10-8zM7.5 12.3a1.3 1.3 0 1 1 0-2.6 1.3 1.3 0 0 1 0 2.6zm4.5 0a1.3 1.3 0 1 1 0-2.6 1.3 1.3 0 0 1 0 2.6zm4.5 0a1.3 1.3 0 1 1 0-2.6 1.3 1.3 0 0 1 0 2.6z"/></svg>
      <svg viewBox="0 0 24 24" aria-label="Account"><circle cx="12" cy="7" r="5"/><path d="M3 22c0-5 4-8 9-8s9 3 9 8z"/></svg>
    </div>
  </header>

  <nav class="side-nav">
    <div class="nav-item" style="top:18px"><svg viewBox="0 0 24 24"><path d="M12 2 1 12h3v10h6v-6h4v6h6V12h3z"/></svg>Top Tutor</div>
    <div class="nav-item" style="top:72px"><svg viewBox="0 0 24 24"><path d="M3 6l6-2 6 2 6-2v14l-6 2-6-2-6 2z"/><circle cx="12" cy="9" r="3" fill="#1c1a1a"/></svg>Daily English</div>
    <div class="nav-item" style="top:126px"><svg viewBox="0 0 24 24"><path d="M5 2h14v20h-5v-4h-4v4H5zm3 3v2h3V5zm5 0v2h3V5zM8 9v2h3V9zm5 0v2h3V9zm-5 4v2h3v-2zm5 0v2h3v-2z"/></svg>Business</div>
  </nav>

  <aside class="vocab-panel">
    <div class="filter">ALL <svg width="9" height="6" viewBox="0 0 9 6"><path d="M1 1l3.5 3.5L8 1" stroke="#1f1f1f" stroke-width="1.5" fill="none"/></svg></div>
    <div class="expand">EXPAND <svg width="10" height="10" viewBox="0 0 10 10" fill="none" stroke="#1f1f1f" stroke-width="1.4"><path d="M1 4V1h3M6 1h3v3M9 6v3H6M4 9H1V6"/></svg></div>
    <div class="vocab-list">
      <div class="group">
        <div class="group-head"><svg viewBox="0 0 10 10"><circle cx="5" cy="5" r="5" fill="#1f1f1f"/><path d="M5 2v3.3h2.2" stroke="#fff" stroke-width="1.2" fill="none"/></svg>SHORT - TERM MEMORY<span class="help">?</span></div>
        <div class="word">Grab</div>
      </div>
      <div class="group">
        <div class="group-head"><svg viewBox="0 0 10 10"><rect x="2" y="2" width="6" height="6" fill="#1f1f1f"/><path d="M3 0v10M5 0v10M7 0v10M0 3h10M0 5h10M0 7h10" stroke="#1f1f1f" stroke-width=".8"/></svg>WORKING MEMORY<span class="help">?</span></div>
        <div class="word">Cool Down</div>
        <div class="word">Crave</div>
        <div class="word">Go For</div>
        <div class="word">Go-To</div>
        <div class="word">In The Mood For</div>
        <div class="word">Sip</div>
        <div class="word">Soothing</div>
        <div class="word">Stick With</div>
        <div class="word">Throw in / Throw On</div>
      </div>
      <div class="group">
        <div class="group-head"><svg viewBox="0 0 10 10"><rect x="1" y="4.5" width="8" height="5.5" fill="#1f1f1f"/><path d="M3 4.5V3a2 2 0 0 1 4 0v1.5" stroke="#1f1f1f" stroke-width="1.3" fill="none"/></svg>LONG - TERM MEMORY<span class="help">?</span></div>
        <div class="word">Give It A Try</div>
      </div>
    </div>
  </aside>

  <section class="steps" aria-label="Review progress">
    <div class="step-line done" style="left:20px;width:191px"></div>
    <div class="step-line" style="left:211px;width:385px"></div>
    <div class="step done" style="left:20px"><div class="dot">01</div>Review 1</div>
    <div class="step current" style="left:211px"><div class="dot">02</div>Review 2</div>
    <div class="step" style="left:404px"><div class="dot">03</div>Review 3</div>
    <div class="step" style="left:596px"><div class="dot">04</div>Review 4</div>
  </section>

  <section class="word-card">
    <div class="word-title"><svg viewBox="0 0 24 24"><path d="M12 1.5l3.2 6.8 7.3.9-5.4 5 1.4 7.3L12 17.9l-6.5 3.6 1.4-7.3-5.4-5 7.3-.9z"/></svg>Grab</div>
    <div class="cta">Start Vocabulary Review Exercise 3</div>
    <p>The word "grab" is most commonly used as averb, meaning to take something quickly or suddenly. Imagine you're running late for school. You don't have time for breakfast, so you quickly grab an apple from the kitchen and rush out the door. As you reach the bus stop, your friend waves and says, "Hey! Let's grab a coffee after class." Later, when you sit down, your phone starts ringing. You grab it from your bag and answer.</p>
  </section>

  <section class="curve-card">
    <svg viewBox="0 0 988 403" aria-label="Learning curve graph">
      <text x="529" y="28" text-anchor="middle" font-size="20" font-weight="600" fill="#1f1f1f">Learning Curve Graph</text>
      <rect x="30" y="40" width="938" height="68" fill="var(--band-long)"/>
      <rect x="30" y="108" width="938" height="155" fill="var(--band-work)"/>
      <rect x="30" y="263" width="938" height="32" fill="var(--band-short)"/>
      <rect x="30" y="295" width="938" height="30" fill="var(--band-forgot)"/>
      <g font-size="11.5" fill="#1f1f1f">
        <text x="37" y="69">Long-Term Memory</text>
        <text x="36" y="142">Working Memory</text>
        <text x="38" y="282">Short- Term Memory</text>
        <text x="36" y="312">Forgotten Memory</text>
      </g>
      <line x1="28" y1="38" x2="28" y2="355" stroke="#1f1f1f" stroke-width="1.2"/>
      <line x1="18" y1="325" x2="968" y2="325" stroke="#1f1f1f" stroke-width="1.2"/>
      <rect x="156" y="263" width="20" height="62" fill="var(--blue)"/>
      <rect x="249" y="108" width="20" height="217" fill="var(--blue)"/>
      <path d="M176 263 Q236 262 248 325" fill="none" stroke="var(--blue)" stroke-width="1.5" stroke-dasharray="1.5 2.5"/>
      <path d="M269 109 Q400 100 463 325" fill="none" stroke="var(--blue)" stroke-width="1.5" stroke-dasharray="1.5 2.5"/>
      <g stroke="#1f1f1f" stroke-width="1.2">
        <path d="M77 325v9M127 325v9M178 325v9M226 325v9M276 325v9M325 325v9M376 325v9M425 325v9M476 325v9M523 325v9M574 325v9M624 325v9M672 325v9M724 325v9M764 325v9M811 325v9M852 325v9M903 325v9M948 325v9"/>
      </g>
      <g font-size="12" fill="#1f1f1f" text-anchor="middle">
        <text x="77" y="350">18 May</text><text x="127" y="350">12:00</text>
        <text x="180" y="350">19 May</text><text x="227" y="350">12:00</text>
        <text x="272" y="349">20 May</text><text x="326" y="351">12:00</text>
        <text x="377" y="351">21 May</text><text x="425" y="351">12:00</text>
        <text x="476" y="349">22 May</text><text x="523" y="349">12:00</text>
        <text x="574" y="351">23 May</text><text x="624" y="351">12:00</text>
        <text x="686" y="351">24 May</text><text x="722" y="351">12:00</text>
        <text x="766" y="352">25 May</text><text x="810" y="352">12:00</text>
        <text x="855" y="352">26 May</text><text x="901" y="352">12:00</text>
        <text x="945" y="352">27 May</text>
      </g>
      <text x="539" y="384" text-anchor="middle" font-size="15.5" font-weight="600" fill="#1f1f1f">Date Range</text>
    </svg>
  </section>

  <section class="analysis">
    <h2>QuillVane Tutor Learning Analysis</h2>
    <p>Lorem ipsum dolor sit amet, consectetur adipiscing elit. Nam rutrum commodo enim id bibendum. Nunc dignissim risus erat, nec finibus nunc dictum eu. Aliquam sit amet euismod metus, quis malesuada erat. Sed at felis quis nulla feugiat cursus at at dolor. Maecenas pretium aliquet dapibus. Fusce et eleifend massa. Sed convallis ex mi, at lobortis ligula congue vel. Pellentesque pharetra molestie leo, sed vehicula felis commodo molestie.</p>
  </section>

  <footer class="footer">© 2025 | www.quillvane.com</footer>
</body>
</html>
```